Heron Haulage needs Bussiness cards!

Our new trucking company needs business cards!
We need the same design with two different names and emails, everything else it's the same.
I have included our original logo so we can use it for the design.
Note: the logo to be used is the o e with the buffalo on the right side, next to the letters H and H.

Target Market(s)

Trucking, refrigerated transportation, freight

Industry/Entity Type

Business

Contact Information for Business Card

Card #1:
Marcus Whitfield
marcuswhitfield@heronhaulage.example
1-855-317-6094
(956)238-7160
4117 W. Larkin Ave.
Pharr, TX 78590
www.heronhaulage.example

Card#2:
Rosalba Quintero
rosalba@heronhaulage.example
1-855-317-6094
(956)238-7160
4117 W. Larkin Ave.
Pharr, TX 78590
www.heronhaulage.example

Font styles to use
Sans Serif

Colors
0655a3
ec1f27
ffffff

Requirements
Must have
• our logo
Nice to have
• roads on background,

```html
<!DOCTYPE html>
<html lang="en">
<head>
<meta charset="utf-8">
<title>Heron Haulage – Business Card</title>
<link href="https://fonts.googleapis.com/css2?family=Open+Sans:wght@400;600;800&display=swap" rel="stylesheet">
<style>
  :root {
    --navy: #0f3563;
    --blue: #1d4f91;
    --red: #d8232b;
    --white: #ffffff;
    --grey-text: #8a8f96;
    --page: #e9eaec;
    --divider: #dfe3e8;
  }
  * { box-sizing: border-box; margin: 0; padding: 0; }
  html, body { width: 1200px; height: 950px; overflow: hidden; }
  body {
    background: var(--page);
    font-family: "Open Sans", Arial, sans-serif;
    display: flex;
    flex-direction: column;
    align-items: center;
    justify-content: center;
    gap: 50px;
  }
  .card {
    width: 700px;
    height: 400px;
    position: relative;
    overflow: hidden;
    box-shadow: 0 6px 18px rgba(0,0,0,0.18);
  }

  /* Back side */
  .card--back {
    background: var(--navy);
    color: var(--white);
    display: flex;
    flex-direction: column;
    align-items: center;
    justify-content: center;
  }
  .brand {
    display: flex;
    align-items: center;
    gap: 18px;
    font-weight: 800;
    line-height: 1;
  }
  .brand__dot {
    border-radius: 50%;
    flex: none;
  }
  .card--back .brand { font-size: 54px; color: var(--white); }
  .card--back .brand__dot { width: 46px; height: 46px; background: var(--white); }
  .back__web {
    margin-top: 60px;
    font-size: 15px;
    letter-spacing: 5px;
    color: rgba(255,255,255,0.85);
  }

  /* Front side */
  .card--front { background: var(--white); }
  .front__brand {
    position: absolute;
    left: 40px;
    top: 190px;
  }
  .card--front .brand { font-size: 32px; color: var(--navy); gap: 12px; }
  .card--front .brand__dot { width: 34px; height: 34px; background: var(--red); }
  .front__divider {
    position: absolute;
    left: 365px;
    top: 60px;
    width: 1px;
    height: 230px;
    background: var(--divider);
  }
  .contact {
    position: absolute;
    left: 390px;
    top: 70px;
  }
  .contact__name {
    font-size: 22px;
    font-weight: 600;
    color: var(--blue);
    margin-bottom: 12px;
  }
  .contact__address {
    font-size: 13.5px;
    color: var(--grey-text);
    line-height: 1.5;
    margin-bottom: 8px;
  }
  .contact__list { list-style: none; }
  .contact__item {
    display: flex;
    align-items: center;
    gap: 9px;
    font-size: 13.5px;
    color: var(--grey-text);
    line-height: 1.6;
  }
  .contact__icon { width: 13px; height: 13px; flex: none; fill: var(--navy); }
  .front__stripe {
    position: absolute;
    left: 0; right: 0;
    bottom: 34px;
    height: 3px;
    background: var(--red);
  }
  .front__band {
    position: absolute;
    left: 0; right: 0; bottom: 0;
    height: 30px;
    background: var(--navy);
  }
</style>
</head>
<body>

  <section class="card card--back" aria-label="Business card, back">
    <div class="brand">
      <span class="brand__dot"></span>
      <span class="brand__name">Heron Haulage</span>
    </div>
    <p class="back__web">www.heronhaulage.example</p>
  </section>

  <section class="card card--front" aria-label="Business card, front">
    <div class="front__brand">
      <div class="brand">
        <span class="brand__dot"></span>
        <span class="brand__name">Heron Haulage</span>
      </div>
    </div>

    <div class="front__divider"></div>

    <div class="contact">
      <h1 class="contact__name">Marcus Whitfield</h1>
      <p class="contact__address">4117 W. Larkin Ave.<br>Pharr, TX 78590</p>
      <ul class="contact__list">
        <li class="contact__item">
          <svg class="contact__icon" viewBox="0 0 16 16"><path d="M3 1h3l1.5 4-2 1.2a9 9 0 0 0 4.3 4.3L11 8.5l4 1.5v3a2 2 0 0 1-2 2A12 12 0 0 1 1 3a2 2 0 0 1 2-2z"/></svg>
          1-855-317-6094
        </li>
        <li class="contact__item">
          <svg class="contact__icon" viewBox="0 0 16 16"><path d="M4.5 0h7A1.5 1.5 0 0 1 13 1.5v13a1.5 1.5 0 0 1-1.5 1.5h-7A1.5 1.5 0 0 1 3 14.5v-13A1.5 1.5 0 0 1 4.5 0zM5 2v10h6V2zm3 11a1 1 0 1 0 0 2 1 1 0 0 0 0-2z"/></svg>
          (956)238-7160
        </li>
        <li class="contact__item">
          <svg class="contact__icon" viewBox="0 0 16 16"><path d="M0 3h16v10H0zm1.5 1.3V12h13V4.3L8 9z"/><path d="M1 3l7 5 7-5z"/></svg>
          marcuswhitfield@heronhaulage.example
        </li>
        <li class="contact__item">
          <svg class="contact__icon" viewBox="0 0 16 16"><circle cx="8" cy="8" r="7" fill="none" stroke="#0f3563" stroke-width="1.6"/><path d="M1 8h14M8 1c-3 3.5-3 10.5 0 14M8 1c3 3.5 3 10.5 0 14" fill="none" stroke="#0f3563" stroke-width="1.2"/></svg>
          www.heronhaulage.example
        </li>
      </ul>
    </div>

    <div class="front__stripe"></div>
    <div class="front__band"></div>
  </section>

</body>
</html>
```